Consulting company business cards

We have a base design, but would be willing to update. We have a new logo/"tag" that needs to be added. Current business card design is attached for reference into our "style."

Industry/Entity Type

Business

Contact Information for Business Card

Should contain name and title, office number, mobile number if appropriate, e-mail, website, physical address, and company logo.

Font styles to use
Other font styles liked:
• See current card design on KorvandBCard

Colors
0455a3
85acd3
aaaaaa

Requirements
Must have
• Our colors are navy blue, gray, and a lighter blue
Nice to have
• Design that I can easily drop in new names/titles as we hire employees.

```html
<!DOCTYPE html>
<html lang="en">
<head>
<meta charset="utf-8">
<title>Brevard Business Card</title>
<link rel="stylesheet" href="https://fonts.googleapis.com/css2?family=Open+Sans:wght@400;600;700&display=swap">
<style>
  :root {
    --backdrop: #e4e6e9;
    --card: #1f2a35;
    --accent-light: #8fe0fb;
    --brand-blue: #0d5a91;
    --tagline: #a9b6c2;
    --text: #ffffff;
  }
  html, body {
    margin: 0;
    padding: 0;
    width: 1200px;
    height: 900px;
    overflow: hidden;
    background: var(--backdrop);
    font-family: "Open Sans", sans-serif;
  }
  .canvas {
    position: relative;
    width: 1200px;
    height: 900px;
  }
  .card {
    position: absolute;
    background: var(--card);
    box-shadow: 0 6px 18px rgba(0,0,0,0.25);
  }
  .card-front {
    left: 238px;
    top: 62px;
    width: 555px;
    height: 343px;
  }
  .card-back {
    left: 457px;
    top: 518px;
    width: 560px;
    height: 343px;
  }
  .emblem-mark {
    position: absolute;
    left: 318px;
    top: 138px;
    width: 0;
  }
  .front-emblem {
    position: absolute;
    left: 86px;
    top: 82px;
    width: 160px;
    height: 160px;
    border-radius: 50%;
    background: var(--accent-light);
  }
  .contact {
    position: absolute;
    left: 296px;
    top: 56px;
    color: var(--text);
    font-size: 14.5px;
    line-height: 23px;
  }
  .contact-name {
    margin: 0;
    color: var(--accent-light);
    font-weight: 600;
    font-size: 20px;
    line-height: 26px;
  }
  .contact-title {
    margin: 0 0 14px;
    font-size: 14.5px;
  }
  .contact-address {
    margin: 0 0 16px;
    font-style: normal;
  }
  .contact-list {
    list-style: none;
    margin: 0;
    padding: 0;
  }
  .contact-list li {
    display: flex;
    align-items: center;
    gap: 8px;
  }
  .contact-list svg {
    width: 12px;
    height: 12px;
    fill: var(--text);
    flex: none;
  }
  .brand {
    position: absolute;
    left: 0;
    right: 0;
    top: 112px;
    text-align: center;
  }
  .brand-lockup {
    display: inline-flex;
    align-items: center;
    gap: 14px;
  }
  .brand-name {
    color: var(--brand-blue);
    font-weight: 700;
    font-size: 66px;
    line-height: 76px;
    letter-spacing: 3px;
  }
  .brand-dot {
    width: 62px;
    height: 62px;
    border-radius: 50%;
    background: var(--accent-light);
  }
  .brand-tagline {
    margin: 2px 0 0;
    color: var(--tagline);
    font-size: 16px;
    letter-spacing: 2.4px;
  }
</style>
</head>
<body>
<main class="canvas">
  <section class="card card-front">
    <div class="front-emblem" role="img" aria-label="Brevard emblem"></div>
    <div class="contact">
      <h1 class="contact-name">Dana Korvand</h1>
      <p class="contact-title">Office Manager</p>
      <address class="contact-address">1835 W 48th St Marion<br>Ohio 43302</address>
      <ul class="contact-list">
        <li>
          <svg viewBox="0 0 24 24" aria-hidden="true"><path d="M6.6 10.8a15 15 0 0 0 6.6 6.6l2.2-2.2a1 1 0 0 1 1-.25 11.4 11.4 0 0 0 3.6.57 1 1 0 0 1 1 1V20a1 1 0 0 1-1 1A17 17 0 0 1 3 4a1 1 0 0 1 1-1h3.5a1 1 0 0 1 1 1c0 1.25.2 2.45.57 3.6a1 1 0 0 1-.25 1z"/></svg>
          555.204.1180
        </li>
        <li>
          <svg viewBox="0 0 24 24" aria-hidden="true"><path d="M7 2h10v5H7zM4 8h16a2 2 0 0 1 2 2v8h-4v4H6v-4H2v-8a2 2 0 0 1 2-2zm4 8v4h8v-4z"/></svg>
          555.204.1195
        </li>
        <li>
          <svg viewBox="0 0 24 24" aria-hidden="true"><path d="M2 5h20v14H2zm2 2v.5l8 5 8-5V7l-8 5z"/></svg>
          dkorvand@brevardtech.com
        </li>
        <li>
          <svg viewBox="0 0 24 24" aria-hidden="true"><path d="M12 2a10 10 0 1 0 0 20 10 10 0 0 0 0-20zm-1 17.9A8 8 0 0 1 4.1 10L9 15v1a2 2 0 0 0 2 2zm6.9-2.5A2 2 0 0 0 16 16h-1v-3a1 1 0 0 0-1-1H8v-2h2a1 1 0 0 0 1-1V7h2a2 2 0 0 0 2-2v-.4a8 8 0 0 1 2.9 12.8z"/></svg>
          brevardtech.com
        </li>
      </ul>
    </div>
  </section>

  <section class="card card-back">
    <div class="brand">
      <div class="brand-lockup">
        <span class="brand-name">BREVARD</span>
        <span class="brand-dot" aria-hidden="true"></span>
      </div>
      <p class="brand-tagline">A CLOUD CONSULTING COMPANY</p>
    </div>
  </section>
</main>
</body>
</html>
```